Business Card Design

We need a business card designed for our new company. Prefer a black card with white logo & writing.

Contact Information for Business Card

Ted Galloway, address: 7-4812 Fernhollow Road, Abbotsford, BC, V3K 8R2, Office Phone: 604-712-3390, Cell: 604-947-2164, Email: ted@resinworkshub.ca

Colors

Designer to choose only greyscale colors for use in the design.

```html
<!DOCTYPE html>
<html lang="en">
<head>
<meta charset="utf-8">
<title>Resin Works Hub – Business Card</title>
<link href="https://fonts.googleapis.com/css2?family=Montserrat:wght@400;500;600;700&display=swap" rel="stylesheet">
<style>
  :root {
    --page-bg: #e7e4df;
    --card-dark: #141414;
    --card-mid: #2a2a2a;
    --text-warm: #d6cdbf;
    --text-soft: #c4bcb0;
    --disc-light: #d9d3c9;
    --disc-ink: #1c1c1c;
  }
  * { margin: 0; padding: 0; box-sizing: border-box; }
  html, body {
    width: 1200px;
    height: 1047px;
    overflow: hidden;
    background: var(--page-bg);
    font-family: "Montserrat", sans-serif;
  }
  .card {
    position: absolute;
    left: 80px;
    top: 242px;
    width: 1040px;
    height: 562px;
    border-radius: 24px;
    background: linear-gradient(100deg, var(--card-dark) 0%, var(--card-mid) 45%, var(--card-dark) 100%);
    box-shadow: 0 18px 40px rgba(0,0,0,0.25);
    overflow: hidden;
    color: var(--text-soft);
  }
  .brand-name {
    position: absolute;
    left: 42px;
    top: 92px;
    font-weight: 700;
    font-size: 34px;
    letter-spacing: 1px;
    color: var(--text-warm);
    line-height: 1;
  }
  .person-name {
    position: absolute;
    left: 42px;
    top: 242px;
    font-weight: 600;
    font-size: 42px;
    color: var(--text-warm);
  }
  .address {
    position: absolute;
    left: 42px;
    top: 324px;
    font-weight: 400;
    font-size: 25px;
    line-height: 42px;
  }
  .contacts {
    position: absolute;
    left: 42px;
    top: 424px;
    list-style: none;
    font-size: 25px;
    line-height: 39px;
  }
  .contacts li { display: flex; align-items: center; gap: 10px; }
  .contacts svg { width: 20px; height: 20px; fill: var(--text-soft); flex: none; }
  .brand-disc {
    position: absolute;
    left: 480px;
    top: 17px;
    width: 534px;
    height: 534px;
    border-radius: 50%;
    background: var(--disc-light);
    display: flex;
    align-items: center;
    justify-content: center;
  }
  .brand-disc span {
    font-weight: 700;
    font-size: 46px;
    letter-spacing: 1px;
    color: var(--disc-ink);
  }
</style>
</head>
<body>
  <div class="card">
    <div class="brand-name">RESIN WORKS HUB</div>

    <div class="person-name">Ted Galloway</div>

    <p class="address">7-4812 Fernhollow Road,<br>Abbotsford, BC, V3K 8R2</p>

    <ul class="contacts">
      <li>
        <svg viewBox="0 0 24 24" aria-hidden="true"><path d="M6.6 10.8a15.1 15.1 0 0 0 6.6 6.6l2.2-2.2c.3-.3.7-.4 1-.2 1.1.4 2.3.6 3.6.6.6 0 1 .4 1 1V20c0 .6-.4 1-1 1A17 17 0 0 1 3 4c0-.6.4-1 1-1h3.5c.6 0 1 .4 1 1 0 1.3.2 2.5.6 3.6.1.3 0 .7-.2 1z"/></svg>
        604-712-3390
      </li>
      <li>
        <svg viewBox="0 0 24 24" aria-hidden="true"><path d="M7 1h10a2 2 0 0 1 2 2v18a2 2 0 0 1-2 2H7a2 2 0 0 1-2-2V3a2 2 0 0 1 2-2zm0 3v14h10V4zm5 15.5a1.2 1.2 0 1 0 0 2.4 1.2 1.2 0 0 0 0-2.4z"/></svg>
        604-947-2164
      </li>
      <li>
        <svg viewBox="0 0 24 24" aria-hidden="true"><path d="M3 5h18a1 1 0 0 1 1 1v12a1 1 0 0 1-1 1H3a1 1 0 0 1-1-1V6a1 1 0 0 1 1-1zm1 2.2V17h16V7.2l-8 5.3z"/></svg>
        ted@resinworkshub.ca
      </li>
    </ul>

    <div class="brand-disc"><span>RESIN WORKS HUB</span></div>
  </div>
</body>
</html>
```